Woman owned consulting company needs an elegant and modern business card design

I need a business card design for my new consulting company, Mara Quillon Consulting. I am looking for something that is simple and elegant, but also creative and original. You can use either version of the logo that are attached. I have also included the information that needs to be featured on the business card.

Contact Information for Business Card

Requirements
Must have
• The logo and the font type and a standard business card size. Use shades of gray/silver and or rose gold that are in the logo.
• I didn't realize that my actual logo wasn't attached. Please incorporate in the designs.
Should not have
• Colors that are different from my logo

```html
<!DOCTYPE html>
<html lang="en">
<head>
<meta charset="utf-8">
<title>Mara Quillon Consulting — Business Card</title>
<link rel="stylesheet" href="https://fonts.googleapis.com/css2?family=Cinzel:wght@500;600&family=Lora:wght@400&display=swap">
<style>
  :root {
    --backdrop: #4a4a4a;
    --card: #1c1c1e;
    --silver: #c9c9cc;
    --silver-soft: #a8a8ac;
    --ink-light: #e6e6e8;
  }
  * { box-sizing: border-box; margin: 0; padding: 0; }
  html, body {
    width: 799px; height: 1200px; overflow: hidden;
    background: var(--backdrop);
  }
  .sheet {
    position: relative; width: 799px; height: 1200px;
    display: flex; flex-direction: column; align-items: center; justify-content: space-around;
    padding: 50px 0;
  }
  .card {
    position: relative;
    width: 640px; height: 366px;
    background: var(--card);
    border-radius: 4px;
    box-shadow: 0 18px 40px rgba(0,0,0,0.45);
  }
  .card-front {
    display: flex; align-items: center; justify-content: center;
  }
  .brand-name {
    font-family: "Cinzel", serif;
    font-weight: 500;
    color: var(--silver);
    text-align: center;
    line-height: 1.15;
    letter-spacing: 2px;
  }
  .card-front .brand-name { font-size: 44px; }
  .card-back {
    display: flex; align-items: center;
    padding: 0 48px;
  }
  .card-back .brand-name {
    font-size: 30px;
    width: 240px;
    text-align: left;
  }
  .contact-block { margin-left: 34px; margin-top: 40px; }
  .person-name {
    font-family: "Cinzel", serif; font-weight: 600;
    font-size: 21px; letter-spacing: 1.5px;
    color: var(--ink-light);
  }
  .person-role {
    font-family: "Lora", serif; font-size: 13px;
    color: var(--silver-soft); margin-bottom: 16px;
  }
  .contact-list { list-style: none; }
  .contact-item {
    display: flex; align-items: center; gap: 10px;
    font-family: "Lora", serif; font-size: 14px;
    color: var(--ink-light); margin-bottom: 6px;
  }
  .contact-icon { width: 13px; height: 13px; fill: var(--ink-light); flex: none; }
</style>
</head>
<body>
<main class="sheet">
  <section class="card card-front" aria-label="Card front">
    <p class="brand-name">Mara Quillon<br>Consulting</p>
  </section>

  <section class="card card-back" aria-label="Card back">
    <p class="brand-name">Mara Quillon<br>Consulting</p>
    <div class="contact-block">
      <h1 class="person-name">MARA QUILLON</h1>
      <p class="person-role">Owner</p>
      <ul class="contact-list">
        <li class="contact-item">
          <svg class="contact-icon" viewBox="0 0 16 16" aria-hidden="true"><path d="M3 1h3l1 4-2 1a9 9 0 0 0 5 5l1-2 4 1v3a2 2 0 0 1-2 2A13 13 0 0 1 1 3a2 2 0 0 1 2-2z"/></svg>
          610-555-0147
        </li>
        <li class="contact-item">
          <svg class="contact-icon" viewBox="0 0 16 16" aria-hidden="true"><path d="M1 3h14v10H1z M2 4l6 5 6-5" fill="none" stroke="#e6e6e8" stroke-width="1.4"/></svg>
          mara@maraquillonconsulting.com
        </li>
        <li class="contact-item">
          <svg class="contact-icon" viewBox="0 0 16 16" aria-hidden="true"><g fill="none" stroke="#e6e6e8" stroke-width="1.3"><circle cx="8" cy="8" r="6.5"/><ellipse cx="8" cy="8" rx="3" ry="6.5"/><path d="M1.5 8h13"/></g></svg>
          www.maraquillonconsulting.com
        </li>
      </ul>
    </div>
  </section>
</main>
</body>
</html>
```